Cosmetic oil label design

We need a label for a cosmetic oganic Argan Oil. The oil is organic imported from Morocco, cold pressed without any preservatives. The lable is for our round 30ml Airless Bottle with clear body Matte Gold Cap, Shiny Gold Collar. We want to communicate that our product is organic natural and works for all beauty needs. We want the emphasis on the words No preservatives, additives or perfumes
We have attached a picture of the bottle and our compnay's logo.

the bottle demensions are Width/Front: 33.0mm
Length/Depth: 33.0mm
Height: 115.0mm
Lable demensions: Lenght 4inch, width 1.75inch.

let us know if you need any other information, cheers!
Updates

Target Market(s)

Our target customer is mainly women 16-70, and also men or anyone looking to have healthy skin and hair using natural products

Industry/Entity Type

Product

Requirements
Must have
• Front side must have:
- attached logo
-words: Authentic Moroccan Argan Oil, No preservatives, additives or perfumes,
L’Huile d’Argan, Produit du Maroc, Imported from Morocco, 30ml

Back side
-Ingredients: 100% Pure Argania Spinosa (Argan Oil)
-Directions: Message into skin, hair or desired area until completely absorbed
-Manufactured for and distributed by Velora Traders
482 W 97th street New York , NY 10027
Nice to have
• Would be nice if we can fit the following information in the back of the label

Rich in vitamin E and essential fatty acids,Argan oil has several benefits. It Hydrates and nourishes skin and hair. Can be used for treating dry skin, split ends softening cuticles. It works for all types of skin.

```html
<!DOCTYPE html>
<html lang="en">
<head>
<meta charset="utf-8">
<title>Argan Oil Label – Back</title>
<link rel="stylesheet" href="https://fonts.googleapis.com/css2?family=Alegreya+Sans:wght@400;500&display=swap">
<style>
  :root {
    --brown-deep: #22190f;
    --brown-dark: #3a2a18;
    --brown-mid: #7a5a32;
    --gold-bright: #eab963;
    --gold-soft: #dcae62;
    --oval-fill: #231a14;
    --gold-text: #e9b761;
    --ink: #2a2119;
    --band: #221a15;
  }
  html, body {
    margin: 0;
    padding: 0;
    width: 1200px;
    height: 2743px;
    overflow: hidden;
    background: var(--brown-deep);
  }
  .label {
    position: relative;
    width: 1200px;
    height: 2743px;
    overflow: hidden;
    font-family: "Alegreya Sans", "Trebuchet MS", sans-serif;
    background: linear-gradient(to bottom,
      var(--brown-deep) 0%,
      var(--brown-dark) 12%,
      var(--brown-mid) 26%,
      var(--gold-bright) 46%,
      var(--gold-soft) 62%,
      #b68d53 78%,
      #6a5034 90%,
      var(--brown-dark) 95%);
  }
  .oval-art {
    position: absolute;
    left: 0;
    top: 0;
    width: 1200px;
    height: 1650px;
  }
  .benefits {
    position: absolute;
    left: 0;
    right: 0;
    top: 135px;
    margin: 0;
    text-align: center;
    color: var(--gold-text);
    font-size: 68px;
    line-height: 95.3px;
    font-weight: 400;
  }
  .benefits span { display: block; }
  .info {
    position: absolute;
    left: 0;
    right: 0;
    text-align: center;
    color: var(--ink);
    margin: 0;
  }
  .info h2 {
    margin: 0;
    font-size: 64px;
    line-height: 87px;
    font-weight: 500;
  }
  .info p {
    margin: 0;
    font-size: 62px;
    line-height: 87px;
  }
  .ingredients { top: 1652px; }
  .directions { top: 1951px; }
  .distributor {
    top: 2338px;
    font-size: 58px;
    line-height: 75px;
    color: #3a2c20;
  }
  .origin-band {
    position: absolute;
    left: 0;
    right: 0;
    bottom: 0;
    height: 133px;
    background: var(--band);
    color: var(--gold-text);
    font-size: 62px;
    line-height: 125px;
    text-align: center;
  }
</style>
</head>
<body>
<div class="label">
  <svg class="oval-art" viewBox="0 0 1200 1650" xmlns="http://www.w3.org/2000/svg">
    <defs>
      <filter id="halo" x="-30%" y="-30%" width="160%" height="160%">
        <feGaussianBlur stdDeviation="45"/>
      </filter>
    </defs>
    <ellipse class="oval-halo" cx="600" cy="770" rx="490" ry="780" fill="#f0c06a" opacity="0.75" filter="url(#halo)"/>
    <ellipse class="oval-panel" cx="600" cy="791" rx="457" ry="745" fill="#231a14"/>
    <g role="img" aria-label="Small heart-shaped leaf flourish on the left of the oval">
      <ellipse cx="160" cy="1240" rx="70" ry="32" fill="#231a14"/>
    </g>
    <g role="img" aria-label="Small heart-shaped leaf flourish on the right of the oval">
      <ellipse cx="1040" cy="1240" rx="70" ry="32" fill="#231a14"/>
    </g>
  </svg>

  <p class="benefits">
    <span>Rich in</span>
    <span>vitamin E</span>
    <span>and essential</span>
    <span>fatty acids,</span>
    <span>Argan oil has</span>
    <span>several benefits.</span>
    <span>It hydrates &amp; nourishes</span>
    <span>skin &amp; hair, Can</span>
    <span>be used for treating</span>
    <span>dry skin, split ends</span>
    <span>softening cuticles.</span>
    <span>It works for</span>
    <span>all types</span>
    <span>of skin</span>
  </p>

  <section class="info ingredients">
    <h2>Ingredients</h2>
    <p>100% Pure Argania Spinosa</p>
    <p>(Argan Oil)</p>
  </section>

  <section class="info directions">
    <h2>Directions</h2>
    <p>Massage into skin,</p>
    <p>hair or desired area until</p>
    <p>completely absorbed.</p>
  </section>

  <p class="info distributor">
    Manufactured for and distributed<br>
    by Velora Traders 482 W 97th<br>
    street New York , NY 10027
  </p>

  <div class="origin-band">imported from Morocco</div>
</div>
</body>
</html>
```